Business Card Design

We need the business card for our new business based in St. Marys, we manufacture mainly bubble wraps. And we would like the design to use our company logo and also make it easy for people to understand right away we are bubble wrap manufacturer

Industry/Entity Type

Business

Contact Information for Business Card

Cushtane Pty Ltd, 14 Larkin Road Wenmore Park NSW 2795, Tel: 02 9471 5826, Fax: 9471 5839, Dara Oyelaran, General Manager, Mobile :0438 217 564, dara.oyelaran@cushtane.com.au, Website: cushtane.com.au

```html
<!DOCTYPE html>
<html lang="en">
<head>
<meta charset="utf-8">
<title>Cushtane Pty Ltd – Business Card</title>
<link href="https://fonts.googleapis.com/css2?family=Arimo:wght@400;700&display=swap" rel="stylesheet">
<style>
  :root {
    --brand-red: #b11f25;
    --brand-grey: #58595b;
    --paper: #ffffff;
    --backdrop: #e9e6e2;
    --ink-light: #ffffff;
  }
  * { box-sizing: border-box; margin: 0; padding: 0; }
  html, body { width: 1200px; height: 848px; overflow: hidden; }
  body {
    background: var(--backdrop);
    font-family: "Arimo", Arial, sans-serif;
    position: relative;
  }
  .card {
    position: absolute;
    width: 560px;
    height: 320px;
    border-radius: 24px;
    overflow: hidden;
    box-shadow: 0 10px 28px rgba(0,0,0,0.18);
  }
  .card-front { left: 60px; top: 70px; background: var(--brand-red); }
  .card-back { left: 580px; top: 458px; background: var(--brand-red); }

  /* Front */
  .front-header {
    height: 138px;
    background: var(--paper);
    display: flex;
    flex-direction: column;
    align-items: center;
    justify-content: center;
  }
  .wordmark {
    font-weight: 700;
    letter-spacing: 1px;
    line-height: 1;
  }
  .front-header .wordmark { color: var(--brand-grey); font-size: 44px; }
  .tagline {
    text-transform: uppercase;
    letter-spacing: 4px;
    font-size: 10px;
    margin-top: 10px;
  }
  .front-header .tagline { color: var(--brand-grey); }

  .front-body {
    height: 182px;
    display: flex;
    color: var(--ink-light);
    padding: 26px 30px 0 30px;
  }
  .identity {
    flex: 1;
    text-align: right;
    padding-right: 22px;
  }
  .person-name { font-size: 30px; font-weight: 400; line-height: 1.05; }
  .person-role { font-size: 15px; margin-top: 2px; }
  .address { font-size: 15px; line-height: 1.3; margin-top: 22px; }
  .divider {
    width: 1px;
    background: rgba(255,255,255,0.7);
    height: 126px;
  }
  .contacts {
    list-style: none;
    padding-left: 18px;
    width: 250px;
  }
  .contacts li {
    display: flex;
    align-items: center;
    font-size: 13.5px;
    height: 25px;
  }
  .contact-icon {
    width: 18px;
    height: 18px;
    background: var(--paper);
    margin-right: 9px;
    flex: none;
    display: flex;
    align-items: center;
    justify-content: center;
  }
  .contact-icon svg { width: 12px; height: 12px; fill: var(--brand-red); }

  /* Back */
  .card-back {
    display: flex;
    flex-direction: column;
    align-items: center;
    justify-content: center;
  }
  .card-back .wordmark { color: var(--ink-light); font-size: 60px; }
  .card-back .tagline { color: rgba(255,255,255,0.85); font-size: 12px; letter-spacing: 5px; margin-top: 14px; }
</style>
</head>
<body>

  <section class="card card-front" aria-label="Business card front">
    <header class="front-header">
      <div class="wordmark">CUSHTANE</div>
      <div class="tagline">Bubble Wrap &amp; Cushion Packing</div>
    </header>
    <div class="front-body">
      <div class="identity">
        <div class="person-name">Dara Oyelaran</div>
        <div class="person-role">General Manager</div>
        <div class="address">Cushtane Pty Ltd, 14 Larkin Road<br>Wenmore Park NSW 2795</div>
      </div>
      <div class="divider"></div>
      <ul class="contacts">
        <li><span class="contact-icon"><svg viewBox="0 0 24 24"><path d="M6.6 10.8a15 15 0 0 0 6.6 6.6l2.2-2.2c.3-.3.7-.4 1-.2 1.1.4 2.3.6 3.6.6.6 0 1 .4 1 1V20c0 .6-.4 1-1 1A17 17 0 0 1 3 4c0-.6.4-1 1-1h3.5c.6 0 1 .4 1 1 0 1.3.2 2.5.6 3.6.1.3 0 .7-.2 1z"/></svg></span>02 9471 5826</li>
        <li><span class="contact-icon"><svg viewBox="0 0 24 24"><path d="M7 1h10a2 2 0 0 1 2 2v18a2 2 0 0 1-2 2H7a2 2 0 0 1-2-2V3a2 2 0 0 1 2-2zm0 3v14h10V4zm5 15.5a1.2 1.2 0 1 0 0 2.4 1.2 1.2 0 0 0 0-2.4z"/></svg></span>0438 217 564</li>
        <li><span class="contact-icon"><svg viewBox="0 0 24 24"><path d="M6 2h10l2 2v5h1a3 3 0 0 1 3 3v7h-4v3H6v-3H2v-7a3 3 0 0 1 3-3h1zm2 2v5h8V5l-1-1zm0 11v5h8v-5z"/></svg></span>9471 5839</li>
        <li><span class="contact-icon"><svg viewBox="0 0 24 24"><path d="M12 2a10 10 0 1 0 0 20 10 10 0 0 0 0-20zm6.9 6h-3a15 15 0 0 0-1.3-3.9A8 8 0 0 1 18.9 8zM12 4c.8 1.2 1.5 2.5 1.9 4h-3.8c.4-1.5 1.1-2.8 1.9-4zM4.3 14a8 8 0 0 1 0-4h3.4a16 16 0 0 0 0 4zm.8 2h3a15 15 0 0 0 1.3 3.9A8 8 0 0 1 5.1 16zm3-8h-3a8 8 0 0 1 4.3-3.9C8.8 5.3 8.4 6.6 8.1 8zM12 20c-.8-1.2-1.5-2.5-1.9-4h3.8c-.4 1.5-1.1 2.8-1.9 4zm2.3-6H9.7a14 14 0 0 1 0-4h4.6a14 14 0 0 1 0 4zm.3 5.9c.6-1.2 1-2.5 1.3-3.9h3a8 8 0 0 1-4.3 3.9zm1.7-5.9a16 16 0 0 0 0-4h3.4a8 8 0 0 1 0 4z"/></svg></span>www.cushtane.com.au</li>
        <li><span class="contact-icon"><svg viewBox="0 0 24 24"><path d="M2 5h20v14H2zm2 2v.4l8 5.3 8-5.3V7zm0 2.8V17h16V9.8l-8 5.3z"/></svg></span>dara.oyelaran@cushtane.com.au</li>
      </ul>
    </div>
  </section>

  <section class="card card-back" aria-label="Business card back">
    <div class="wordmark">CUSHTANE</div>
    <div class="tagline">Bubble Wrap &amp; Cushion Packing</div>
  </section>

</body>
</html>
```